TALVORNE End User Instruction Guide

I need to create a 5 to 7-page instruction guides for customers who purchased a phone system from our company. The document is a quick reference guide that will help end-users learn how to set up and use their new desk phone and software applications. I need the guide to be 3 x 5 or 6 x 8 in size and will fold like a book.

Target Market(s)

Business users / Quorblen Desk Phone Users / TalVORNE Portal users

Industry/Entity Type

Telecommunications

Font styles to use
Serif

Colors
0758a5
ffffff

Requirements
Must have
• Need to have step-by-step instructions that include the information from the QuickStart guide I provided. I need to see an image of the phone with an arrow pointing to the key on the phone that should be pressed. For example, when checking voicemail the Messages key is pressed and I want to highlight this button or call it out somehow.

I need to have three pages for setup instructions, one page for shortcuts or features codes and our support contacts on the last page.
Nice to have
• I want to have a page for notes that the end-user can use during training. I would also like to have a blank space next to passwords and user ID's so they can be filled out with specific details that are provided during their training. For example, in the voicemail section, I include a default PIN. I would like to leave this blank and let the end-user fill it out during training.
Should not have
• Complex shapes and designs. I like straight lines and a simple easy to understand layout.

```html
<!DOCTYPE html>
<html lang="en">
<head>
<meta charset="utf-8">
<title>TALVORNE End User Quick Start Guide</title>
<link rel="stylesheet" href="https://fonts.googleapis.com/css2?family=Roboto:wght@300;400;500;700;900&display=swap">
<style>
  :root {
    --brand-blue: #2b4588;
    --band-blue: #1f3f86;
    --slate: #37474a;
    --paper: #ffffff;
    --phone-dark: #2a3036;
    --phone-mid: #4a535b;
  }
  * { margin: 0; padding: 0; box-sizing: border-box; }
  html, body { width: 900px; height: 1200px; overflow: hidden; background: var(--paper); }
  body { font-family: "Roboto", Arial, sans-serif; }
  .cover { position: relative; width: 900px; height: 1200px; background: var(--paper); overflow: hidden; }

  .brand { position: absolute; left: 70px; top: 82px; display: flex; align-items: center; gap: 14px; color: var(--slate); }
  .brand-mark { width: 52px; height: 52px; background: var(--slate); }
  .brand-name { font-weight: 700; line-height: 1; }
  .brand-name .word { display: block; font-size: 38px; letter-spacing: 1px; }
  .brand-name .sub { display: block; font-size: 15px; letter-spacing: 6.4px; margin-top: 4px; }

  .tagline { position: absolute; right: 48px; top: 89px; font-size: 19px; font-weight: 700; color: var(--brand-blue); letter-spacing: 0.2px; }

  .header-band { position: absolute; left: 0; top: 0; }

  .title { position: absolute; left: 0; width: 874px; top: 385px; text-align: center; font-weight: 300; font-size: 74px; line-height: 88px; color: var(--brand-blue); }

  .wedge { position: absolute; left: 0; top: 0; }

  .intro { position: absolute; left: 101px; top: 707px; font-size: 19.5px; font-weight: 300; line-height: 25px; color: var(--paper); text-transform: uppercase; }

  .phone-photo { position: absolute; left: 340px; top: 625px; width: 450px; height: 255px; border-radius: 14px 14px 30px 30px;
    background: linear-gradient(160deg, var(--phone-mid) 0%, var(--phone-dark) 60%, #1b1f23 100%); }

  .contacts { position: absolute; left: 0; top: 1010px; width: 900px; }
  .contact-row { position: absolute; left: 0; width: 900px; height: 28px; }
  .contact-row .bar { position: absolute; top: 9px; height: 10px; }
  .contact-row .bar-left { background: var(--band-blue); }
  .contact-row .bar-right { background: var(--slate); right: 0; }
  .contact-row .text { position: absolute; top: 0; font-size: 19.5px; font-weight: 700; color: var(--brand-blue); line-height: 28px; white-space: nowrap; }
</style>
</head>
<body>
<main class="cover">
  <svg class="header-band" width="900" height="180" aria-hidden="true">
    <defs>
      <linearGradient id="bandFade" x1="0" x2="1" y1="0" y2="0">
        <stop offset="0" stop-color="#1f3f86"/>
        <stop offset="1" stop-color="#37474a"/>
      </linearGradient>
    </defs>
    <polygon points="440,140 900,140 900,170 422,170" fill="url(#bandFade)"/>
  </svg>

  <div class="brand">
    <div class="brand-mark"></div>
    <div class="brand-name">
      <span class="word">TALVORNE</span>
      <span class="sub">COMMUNICATIONS</span>
    </div>
  </div>

  <p class="tagline">AT TalVORNE, WE MAKE IT EASY</p>

  <h1 class="title">End User Quick<br>Start Guide</h1>

  <svg class="wedge" width="900" height="900" aria-hidden="true">
    <polygon points="0,562 900,860 0,860" fill="#37474a"/>
  </svg>

  <p class="intro">To set up and use<br>new desk phone and<br>software applications</p>

  <div class="phone-photo" role="img" aria-label="Photo of a Quorblen desk phone with colour display, handset and keypad"></div>

  <section class="contacts">
    <div class="contact-row" style="top:0">
      <span class="bar bar-left" style="left:0;width:248px"></span>
      <span class="text" style="left:260px">support@talvornecomms.com</span>
      <span class="bar bar-right" style="width:248px"></span>
    </div>
    <div class="contact-row" style="top:40px">
      <span class="bar bar-left" style="left:0;width:366px"></span>
      <span class="text" style="left:386px">555-014-7720</span>
      <span class="bar bar-right" style="width:365px"></span>
    </div>
    <div class="contact-row" style="top:80px">
      <span class="bar bar-left" style="left:5px;width:265px"></span>
      <span class="text" style="left:280px">www.talvornecomms.com</span>
      <span class="bar bar-right" style="width:270px"></span>
    </div>
  </section>
</main>
</body>
</html>
```